Brightfen Business Card Redesign & Logo Update

We need to update our business cards to something more modern and fresh. Brightfen can provide the current color schemes and old design examples, but welcome creativity in helping us with this redesign. PLEASE NOTE that we no longer utilize the "tree" and/or "leaf" imagery in our branding. If able would apprecaite an update on the quality of our "words only" logo in Ai. / PNG formats too.

Target Market(s)

Investors, landowners, corporate partners, contractors

Industry/Entity Type

Environmental Restoration & Conservation

Contact Information for Business Card

Logo, persons name, title, mailing address, phone and email, website url

Font styles to use
Other font styles liked:
• Merriweather

Requirements
Nice to have
• Logo, persons name, title, mailing address, phone and email, website url, but open to ideams
Should not have
• No all back backgrounds

```html
<!DOCTYPE html>
<html lang="en">
<head>
<meta charset="utf-8">
<title>Brightfen Business Card</title>
<link rel="stylesheet" href="https://fonts.googleapis.com/css2?family=Montserrat:wght@500;600;700;800&display=swap">
<style>
  :root {
    --orange: #ea7d27;
    --orange-soft: #f5bd8c;
    --green: #167f3e;
    --ink: #1d1d1d;
    --paper: #ffffff;
    --backdrop: #d9d9d9;
  }
  * { box-sizing: border-box; margin: 0; padding: 0; }
  html, body { width: 1200px; height: 900px; overflow: hidden; }
  body {
    background: var(--backdrop);
    font-family: "Montserrat", Arial, sans-serif;
    position: relative;
  }
  .card {
    position: absolute;
    width: 630px;
    height: 360px;
    box-shadow: 0 10px 28px rgba(0,0,0,0.25);
  }
  /* Front */
  .card-front {
    left: 70px;
    top: 70px;
    background: var(--orange);
    overflow: hidden;
  }
  .card-front .map-area {
    position: absolute;
    left: 70px;
    top: 50px;
    width: 490px;
    height: 260px;
    background: radial-gradient(ellipse at center, var(--orange-soft) 0%, rgba(245,189,140,0.55) 60%, rgba(245,189,140,0) 100%);
    border-radius: 50%;
  }
  .card-front .brand-name {
    position: absolute;
    left: 0; right: 0;
    top: 142px;
    text-align: center;
    font-weight: 800;
    font-size: 72px;
    letter-spacing: 2px;
    color: var(--paper);
  }
  /* Back */
  .card-back {
    left: 500px;
    top: 470px;
    background: var(--paper);
    padding: 36px 40px;
  }
  .card-back .brand-name {
    position: absolute;
    right: 40px;
    top: 34px;
    font-weight: 800;
    font-size: 44px;
    letter-spacing: 1px;
    color: var(--green);
  }
  .person {
    position: absolute;
    left: 40px;
    top: 140px;
  }
  .person-name {
    font-weight: 800;
    font-size: 22px;
    letter-spacing: 0.5px;
  }
  .person-name .first { color: var(--green); }
  .person-name .last { color: var(--orange); }
  .person-title {
    margin-top: 4px;
    font-weight: 500;
    font-size: 15px;
    color: var(--ink);
  }
  .address {
    position: absolute;
    right: 40px;
    top: 150px;
    text-align: right;
    font-weight: 500;
    font-size: 15px;
    line-height: 1.45;
    color: var(--ink);
  }
  .contacts {
    position: absolute;
    left: 40px;
    bottom: 32px;
    list-style: none;
  }
  .contacts li {
    display: flex;
    align-items: center;
    gap: 12px;
    font-weight: 500;
    font-size: 17px;
    color: var(--ink);
    margin-top: 8px;
  }
  .contact-icon {
    width: 24px; height: 24px;
    flex: none;
  }
</style>
</head>
<body>

  <section class="card card-front">
    <div class="map-area" role="img" aria-label="World map silhouette in light orange"></div>
    <div class="brand-name">BRIGHTFEN</div>
  </section>

  <section class="card card-back">
    <div class="brand-name">BRIGHTFEN</div>

    <div class="person">
      <p class="person-name"><span class="first">DANA</span> <span class="last">MERROW</span></p>
      <p class="person-title">Managing Director</p>
    </div>

    <address class="address" style="font-style:normal">
      42 Harlow Lane 7<br>
      Fenwick, NY 12940
    </address>

    <ul class="contacts">
      <li>
        <svg class="contact-icon" viewBox="0 0 24 24" aria-hidden="true">
          <circle cx="12" cy="12" r="12" fill="var(--orange)"/>
          <path d="M8.2 6.5l2 2.2-1.2 1.6c.8 1.7 2 2.9 3.7 3.7l1.6-1.2 2.2 2-1.2 2.2c-4.4-.4-8.1-4.1-8.5-8.5z" fill="#fff"/>
        </svg>
        555-014-2268
      </li>
      <li>
        <svg class="contact-icon" viewBox="0 0 24 24" aria-hidden="true">
          <circle cx="12" cy="12" r="12" fill="var(--orange)"/>
          <rect x="6" y="8" width="12" height="8.5" rx="1" fill="#fff"/>
          <path d="M6.3 8.4L12 13l5.7-4.6" fill="none" stroke="var(--orange)" stroke-width="1.2"/>
        </svg>
        info@brightfen.com
      </li>
      <li>
        <svg class="contact-icon" viewBox="0 0 24 24" aria-hidden="true">
          <circle cx="12" cy="12" r="12" fill="var(--orange)"/>
          <circle cx="12" cy="12" r="6" fill="none" stroke="#fff" stroke-width="1.4"/>
          <ellipse cx="12" cy="12" rx="2.6" ry="6" fill="none" stroke="#fff" stroke-width="1.2"/>
          <path d="M6 12h12" stroke="#fff" stroke-width="1.2"/>
        </svg>
        www.brightfen.com
      </li>
    </ul>
  </section>

</body>
</html>
```